Hvac and insulation company needs good looking business card design

We are hvac and insulation company and looking for a new business cards that look to today standards designs

Target Market(s)

homeowners

Industry/Entity Type

Hvac

Contact Information for Business Card

Name: Walter Brinoku
Home comfort consultant
address: 4827 Dunmore St #215 Oakland, CA 94619
office: 888-316-2790
cell: 510-742-3185
Lic.# 584261
Email: walter@corvane-hvac.com
Web: corvane-hvac.com

Requirements
Must have
• clean and sleek look
Nice to have
• simple with a clean look
Should not have
• to busy business card

```html
<!DOCTYPE html>
<html lang="en">
<head>
<meta charset="utf-8">
<title>Corvane Business Card</title>
<link rel="stylesheet" href="https://fonts.googleapis.com/css2?family=Open+Sans:wght@300;400;600&family=Oswald:wght@500&display=swap">
<style>
  :root {
    --backdrop: #3b3b3b;
    --card: #1f1f1f;
    --ink: #f2f2f2;
    --ink-soft: #9a9a9a;
    --accent: #f39217;
  }
  * { margin: 0; padding: 0; box-sizing: border-box; }
  html, body {
    width: 1200px; height: 900px; overflow: hidden;
    background: var(--backdrop);
    font-family: "Open Sans", Arial, sans-serif;
    color: var(--ink);
  }
  .card {
    position: absolute; left: 250px;
    width: 700px; height: 400px;
    background: var(--card);
  }
  .card--front { top: 35px; }
  .card--back { top: 465px; }

  /* front */
  .brand-mark {
    position: absolute; left: 0; right: 0; top: 140px;
    display: flex; justify-content: center; align-items: center; gap: 16px;
  }
  .brand-dot {
    width: 54px; height: 54px; border-radius: 50%;
    background: #2c2c2c;
  }
  .brand-name {
    font-weight: 600; font-size: 56px; letter-spacing: 2px;
    color: #8c8c8c; line-height: 1;
  }
  .front-web {
    position: absolute; left: 0; right: 0; bottom: 42px;
    display: flex; justify-content: center; align-items: center; gap: 10px;
    font-size: 17px; letter-spacing: 1px; color: var(--ink);
  }
  .front-web .accent { color: var(--accent); }

  /* back */
  .license {
    position: absolute; top: 28px; right: 36px;
    font-size: 16px; letter-spacing: 1px; color: #d8d8d8;
  }
  .identity {
    position: absolute; left: 88px; top: 120px; width: 300px;
    text-align: right;
  }
  .person-name {
    font-family: "Oswald", "Arial Narrow", sans-serif;
    font-weight: 500; font-size: 40px; letter-spacing: 1px;
    text-transform: uppercase; line-height: 1.1;
  }
  .person-role {
    font-weight: 600; font-size: 19px; letter-spacing: 0.5px;
    color: var(--accent);
  }
  .divider {
    position: absolute; left: 408px; top: 118px;
    width: 2px; height: 102px; background: var(--ink);
  }
  .contact-list {
    position: absolute; left: 428px; top: 116px;
    list-style: none;
  }
  .contact-list li {
    display: flex; align-items: center; gap: 14px;
    height: 26px; font-size: 17px; font-weight: 400; letter-spacing: 0.5px;
  }
  .contact-list svg { width: 18px; height: 18px; flex: none; }
  .footer-line {
    position: absolute; left: 88px; bottom: 44px;
    display: flex; align-items: baseline; gap: 10px;
    font-size: 19px; letter-spacing: 1px;
  }
  .footer-brand { color: var(--accent); font-weight: 600; font-size: 22px; }
</style>
</head>
<body>

<section class="card card--front">
  <div class="brand-mark">
    <span class="brand-dot"></span>
    <span class="brand-name">corvane</span>
  </div>
  <p class="front-web">
    <svg width="20" height="20" viewBox="0 0 20 20" fill="none" stroke="#f39217" stroke-width="1.5">
      <circle cx="10" cy="10" r="8"/><ellipse cx="10" cy="10" rx="3.5" ry="8"/>
      <line x1="2" y1="10" x2="18" y2="10"/><line x1="3.5" y1="6" x2="16.5" y2="6"/><line x1="3.5" y1="14" x2="16.5" y2="14"/>
    </svg>
    <span>www.<span class="accent">corvane-hvac</span>.com</span>
  </p>
</section>

<section class="card card--back">
  <p class="license">Lic #584261</p>

  <div class="identity">
    <h1 class="person-name">Walter Brinoku</h1>
    <p class="person-role">Home comfort consultant</p>
  </div>

  <span class="divider"></span>

  <ul class="contact-list">
    <li>
      <svg viewBox="0 0 18 18" fill="none" stroke="#f39217" stroke-width="1.6"><rect x="4.5" y="1.5" width="9" height="15" rx="1.5"/><line x1="7.5" y1="13.5" x2="10.5" y2="13.5"/></svg>
      888 316 2790
    </li>
    <li>
      <svg viewBox="0 0 18 18" fill="#f39217"><path d="M4 2l3 3-1.6 2a9 9 0 0 0 5.6 5.6l2-1.6 3 3-2 2C8 16 2 10 2 4z"/></svg>
      510 742 3185
    </li>
    <li>
      <svg viewBox="0 0 18 18" fill="none" stroke="#f39217" stroke-width="1.6"><rect x="1.5" y="4" width="15" height="10" rx="1"/><path d="M1.5 4.5L9 10l7.5-5.5"/></svg>
      walter@corvane-hvac.com
    </li>
    <li>
      <svg viewBox="0 0 20 20" fill="none" stroke="#f39217" stroke-width="1.5"><circle cx="10" cy="10" r="8"/><ellipse cx="10" cy="10" rx="3.5" ry="8"/><line x1="2" y1="10" x2="18" y2="10"/><line x1="3.5" y1="6" x2="16.5" y2="6"/><line x1="3.5" y1="14" x2="16.5" y2="14"/></svg>
      corvane-hvac.com
    </li>
  </ul>

  <p class="footer-line">
    <span class="footer-brand">corvane</span>
    <span>- 4827 Dunmore St #215 Oakland, CA 94619</span>
  </p>
</section>

</body>
</html>
```